Tidy4all

Full service cleaning company. Specializing in commercial and apartment cleans.
Fully licensed and insured
Digital photos and invoices provided
for every job
For web designer...basic info as expected by a highend cleaning company that provides excellent service at reasonable pricing. We are going after large property management companies as well as not pricing ourselves out to help the local mom and pop companies as well.
Updates

Project Deadline Extended Reason: Everyone seems to be having trouble understanding that we are a dumpster company that is adding a cleaning side to the company. We want our clients to see Tidy4All as a separate branch of our our already established waste management company.We are not a regular cleaning company. We specialize in going after large commercial cleans and apartment cleans. I have now included info regarding a proposal for work and our invoice/job completion to make it clearer what we do Added Monday, July 20, 2015

Target Market(s)

Property Management companies in Savannah, Richmond Hill, Rincon, Hinesville and Midway Georgia

Industry/Entity Type

Cleaning Service

Coding

Coded - Design and coding required

Number of Pages Required

3 page

Requirements
Must have
• Nice home page with lots of photos (stock are fine) to convey exactly what we do (getting logo bid on right now on this sight).
• Information page with employee photos (can leave blank) need room for 4 photos and bios.
• Page or link to a static page for the dumpster company BinRun (logo for this is red and black file attached along with photo of dumpster. This page just needs to be one page with contact info and information about commercial dumpster.
• Basically this site is just a fluff page used for marketing purposes. Its content can be general and once created wont change much. Services and photos can be provided upon request but general layout and info is what we are looking for.

```html
<!DOCTYPE html>
<html lang="en">
<head>
<meta charset="utf-8">
<title>Tidy4All — Full Service Cleaning</title>
<link href="https://fonts.googleapis.com/css2?family=Open+Sans:wght@400;600;700&family=Noto+Serif:wght@700&display=swap" rel="stylesheet">
<style>
:root{
  --red:#e41e26;
  --dark:#111111;
  --ink:#333333;
  --muted:#777777;
  --band:#ececec;
  --field:#dcdcdc;
  --green:#8cc63f;
  --white:#ffffff;
}
*{box-sizing:border-box;margin:0;padding:0}
html,body{width:681px;height:1200px;overflow:hidden}
body{font-family:"Open Sans",Arial,sans-serif;color:var(--ink);background:var(--white);position:relative;font-size:7px;line-height:1.45}
.abs{position:absolute}
h2,h3{font-family:"Noto Serif",Georgia,serif;color:var(--dark);font-weight:700}

/* header */
.brand{left:24px;top:12px;display:flex;align-items:center;gap:7px}
.brand-mark{width:16px;height:16px;background:var(--red)}
.brand-name{font-weight:700;font-size:20px;color:var(--dark);letter-spacing:.2px}
.contact-top{right:20px;top:4px;display:flex;gap:14px;align-items:center;font-size:8px}
.contact-top .mail{display:flex;gap:4px;align-items:center}
.contact-top .phone{background:var(--red);color:var(--white);font-weight:700;font-size:12px;padding:2px 8px;border-radius:3px;display:flex;gap:5px;align-items:center}
.nav{left:210px;right:0;top:28px;height:20px;background:var(--red);display:flex;padding-left:14px}
.nav a{color:var(--white);text-decoration:none;font-size:7.5px;font-weight:600;padding:0 11px;line-height:20px}
.nav a.active{background:var(--dark)}

/* hero */
.hero{left:0;top:50px;width:681px;height:252px;background:linear-gradient(160deg,#c9d6e2 0%,#8d9fb1 40%,#4b5968 75%,#2b333d 100%)}
.hero-text{right:40px;top:120px;color:var(--white);font-family:"Noto Serif",Georgia,serif;font-weight:700;font-size:15px;line-height:1.25;text-shadow:0 1px 2px rgba(0,0,0,.5)}
.hero-dots{left:312px;top:284px;display:flex;gap:4px}
.hero-dots span{width:6px;height:6px;border-radius:50%;background:#555}
.hero-dots span:first-child{background:#222}

/* services */
.services{left:0;top:302px;width:681px;height:258px;background:var(--band)}
.card{top:322px;width:190px;height:222px;background:var(--white);border-top:3px solid var(--red);padding:8px 10px;box-shadow:0 1px 3px rgba(0,0,0,.15)}
.card h3{font-size:11px;margin-bottom:6px}
.card .photo{height:70px;margin-bottom:7px}
.card p{font-size:6.5px;color:var(--muted)}
.more{color:var(--red);font-weight:700;font-size:6px;text-align:right;display:block;margin-top:6px}

/* welcome */
.welcome{left:24px;top:580px;width:390px}
.welcome h2,.schedule h2{font-size:12px;margin-bottom:8px}
.welcome p{font-size:6.5px;color:var(--muted);margin-bottom:8px}
.schedule{left:460px;top:580px;width:197px}
.schedule .field{height:13px;background:var(--field);margin-bottom:5px;font-size:5.5px;color:#888;padding:2px 4px}
.schedule .row{display:flex;gap:5px}
.schedule .row .field{flex:1}
.schedule .msg{height:26px}
.schedule .btn{background:var(--red);color:var(--white);font-size:6px;font-weight:700;width:36px;text-align:center;padding:2px;margin-left:auto}

/* features */
.features{left:0;top:770px;width:681px;height:262px;background:var(--band)}
.feature{top:785px;width:180px}
.feature h3{font-size:10px;margin-bottom:6px}
.feature .photo{height:78px;margin-bottom:6px}
.feature p{font-size:6px;color:var(--muted)}
.why li{list-style:none;font-size:6px;color:var(--ink);display:flex;gap:5px;align-items:center;margin-bottom:6px}

/* cta */
.cta{left:24px;top:965px;width:633px;height:48px;background:var(--green);display:flex;align-items:center;justify-content:center;gap:10px}
.cta p{font-family:"Noto Serif",Georgia,serif;font-weight:700;color:var(--white);font-size:10px}
.cta .btn{background:var(--dark);color:var(--white);font-size:6px;font-weight:700;padding:4px 8px}

/* footer */
.footer{left:0;top:1032px;width:681px;height:150px;background:var(--dark);color:#cfcfcf}
.fcol{top:1040px}
.fcol h4{color:var(--white);font-size:8px;font-weight:600;margin-bottom:6px}
.fcol li{list-style:none;font-size:6px;margin-bottom:3px}
.fcol .line{display:flex;gap:5px;align-items:flex-start;font-size:6px;margin-bottom:6px}
.footer-brand{right:30px;top:1110px;font-weight:700;font-size:22px;color:#3a3a3a}
.copy{left:0;top:1182px;width:681px;height:18px;background:#000;color:#888;font-size:6px;padding:5px 24px}
</style>
</head>
<body>

<header>
  <div class="abs brand"><span class="brand-mark"></span><span class="brand-name">Tidy4All</span></div>
  <div class="abs contact-top">
    <span class="mail">
      <svg width="9" height="7" viewBox="0 0 9 7"><rect x=".5" y=".5" width="8" height="6" fill="none" stroke="#e41e26"/><path d="M.5 .5 4.5 4 8.5 .5" fill="none" stroke="#e41e26"/></svg>
      info@tidy4all.com
    </span>
    <span class="phone">
      <svg width="9" height="9" viewBox="0 0 24 24"><path fill="#fff" d="M6.6 10.8a15 15 0 0 0 6.6 6.6l2.2-2.2a1 1 0 0 1 1-.25 11.4 11.4 0 0 0 3.6.6 1 1 0 0 1 1 1V20a1 1 0 0 1-1 1A17 17 0 0 1 3 4a1 1 0 0 1 1-1h3.5a1 1 0 0 1 1 1c0 1.25.2 2.45.6 3.6a1 1 0 0 1-.25 1z"/></svg>
      123-456-7890
    </span>
  </div>
  <nav class="abs nav">
    <a class="active" href="#">Home</a><a href="#">About Us</a><a href="#">Services</a><a href="#">Think Green</a><a href="#">Customer Stories</a><a href="#">Contact Us</a>
  </nav>
</header>

<section>
  <div class="abs hero" role="img" aria-label="Looking up at glass office towers against the sky"></div>
  <p class="abs hero-text">We Are A Full Service<br>Cleaning Company<br>Specializing in commercial<br>and apartment cleans</p>
  <div class="abs hero-dots"><span></span><span></span><span></span><span></span></div>
</section>

<section>
  <div class="abs services"></div>
  <article class="abs card" style="left:24px">
    <h3>Home Owner</h3>
    <div class="photo" role="img" aria-label="Dumpster filled with household debris" style="background:linear-gradient(135deg,#8a7a5c,#5d6a4c)"></div>
    <p>Lorem ipsum dolor sit amet, consectetuer adipiscing elit. Praesent volutpat ultrices euismod. Mauris consectetur tellus quis nam dictum pharetra.</p>
    <span class="more">READ MORE &gt;</span>
  </article>
  <article class="abs card" style="left:245px">
    <h3>Business Owner</h3>
    <div class="photo" role="img" aria-label="Large orange roll-off dumpster at a work site" style="background:linear-gradient(135deg,#c7782f,#7c5a3a)"></div>
    <p>Lorem ipsum dolor sit amet, consectetuer adipiscing elit. Praesent volutpat ultrices euismod. Mauris consectetur tellus quis nam dictum pharetra.</p>
    <span class="more">READ MORE &gt;</span>
  </article>
  <article class="abs card" style="left:467px">
    <h3>Rent-a-Dumpster</h3>
    <div class="photo" role="img" aria-label="Blue rental dumpster beside a building" style="background:linear-gradient(135deg,#e6ebef,#6e8aa6)"></div>
    <p>Lorem ipsum dolor sit amet, consectetuer adipiscing elit. Praesent volutpat ultrices euismod. Mauris consectetur tellus quis nam dictum pharetra.</p>
    <span class="more">READ MORE &gt;</span>
  </article>
</section>

<section>
  <div class="abs welcome">
    <h2>Welcome To Tidy4All</h2>
    <p>Lorem ipsum dolor sit amet, consectetuer adipiscing elit, sed diam nonummy nibh euismod tincidunt ut laoreet dolore magna aliquam erat volutpat. Ut wisi enim ad minim veniam, quis nostrud exerci tation ullamcorper suscipit lobortis nisl ut aliquip ex ea commodo consequat.</p>
    <p>Lorem ipsum dolor sit amet, consectetuer adipiscing elit, sed diam nonummy nibh euismod tincidunt ut laoreet dolore magna aliquam erat volutpat. Ut wisi enim ad minim veniam, quis nostrud exerci tation ullamcorper suscipit lobortis nisl ut aliquip ex ea commodo consequat.</p>
    <span class="more">READ MORE &gt;</span>
  </div>
  <form class="abs schedule">
    <h2>Schedule A Service</h2>
    <div class="field">Name</div>
    <div class="field">Pick up Date</div>
    <div class="row"><div class="field">Drop Off Date</div><div class="field">Time</div></div>
    <div class="field">Email</div>
    <div class="field msg">Message</div>
    <div class="btn">SUBMIT</div>
  </form>
</section>

<section>
  <div class="abs features"></div>
  <div class="abs feature" style="left:24px">
    <h3>24/7 Access</h3>
    <div class="photo" role="img" aria-label="Round-the-clock service sign" style="background:linear-gradient(135deg,#5f7d96,#2d3f52)"></div>
    <p>Lorem ipsum dolor sit amet, consecte adipisci elit sed diam nonumm. Euismod tincidunt laoreet dolore magna aliquam.</p>
  </div>
  <div class="abs feature" style="left:250px">
    <h3>Reliable. Clean. Safe.</h3>
    <div class="photo" role="img" aria-label="Row of green commercial dumpsters" style="background:linear-gradient(135deg,#9cc36b,#3f7a2c)"></div>
    <p>Lorem ipsum dolor sit amet, consecte adipisci elit sed diam nonumm. Euismod tincidunt laoreet dolore magna aliquam.</p>
  </div>
  <div class="abs feature why" style="left:470px">
    <h3>Why Choose Us</h3>
    <ul>
      <li><svg width="7" height="7" viewBox="0 0 8 8"><path d="M1 4l2 2 4-5" fill="none" stroke="#e41e26" stroke-width="1.5"/></svg>Wide selection of dumpster sizes available</li>
      <li><svg width="7" height="7" viewBox="0 0 8 8"><path d="M1 4l2 2 4-5" fill="none" stroke="#e41e26" stroke-width="1.5"/></svg>Flexible, timely pickup and delivery</li>
      <li><svg width="7" height="7" viewBox="0 0 8 8"><path d="M1 4l2 2 4-5" fill="none" stroke="#e41e26" stroke-width="1.5"/></svg>Fast service available</li>
      <li><svg width="7" height="7" viewBox="0 0 8 8"><path d="M1 4l2 2 4-5" fill="none" stroke="#e41e26" stroke-width="1.5"/></svg>Easy online ordering and scheduling</li>
      <li><svg width="7" height="7" viewBox="0 0 8 8"><path d="M1 4l2 2 4-5" fill="none" stroke="#e41e26" stroke-width="1.5"/></svg>Online account management</li>
      <li><svg width="7" height="7" viewBox="0 0 8 8"><path d="M1 4l2 2 4-5" fill="none" stroke="#e41e26" stroke-width="1.5"/></svg>Instant online pricing</li>
    </ul>
  </div>
  <div class="abs cta">
    <p>Ready to get started? See what dumpsters are available in your area.</p>
    <span class="btn">SHOW PRODUCTS</span>
  </div>
</section>

<footer>
  <div class="abs footer"></div>
  <div class="abs fcol" style="left:24px">
    <h4>Quick Links</h4>
    <ul><li>Home</li><li>About Us</li><li>Services</li><li>Think Green</li><li>Customer Stories</li><li>Contact Us</li></ul>
  </div>
  <div class="abs fcol" style="left:150px;width:140px">
    <h4>Contact Information</h4>
    <div class="line"><svg width="6" height="8" viewBox="0 0 6 8"><path d="M3 0a3 3 0 0 0-3 3c0 2 3 5 3 5s3-3 3-5a3 3 0 0 0-3-3z" fill="#e41e26"/></svg>Lorem ipsum dolor sit amet, 100 Main Street, Anytown, GA 00000</div>
    <div class="line"><svg width="7" height="7" viewBox="0 0 24 24"><path fill="#e41e26" d="M6.6 10.8a15 15 0 0 0 6.6 6.6l2.2-2.2a1 1 0 0 1 1-.25 11.4 11.4 0 0 0 3.6.6 1 1 0 0 1 1 1V20a1 1 0 0 1-1 1A17 17 0 0 1 3 4a1 1 0 0 1 1-1h3.5a1 1 0 0 1 1 1c0 1.25.2 2.45.6 3.6a1 1 0 0 1-.25 1z"/></svg>123-456-7890</div>
    <div class="line"><svg width="8" height="6" viewBox="0 0 9 7"><rect x=".5" y=".5" width="8" height="6" fill="none" stroke="#e41e26"/><path d="M.5 .5 4.5 4 8.5 .5" fill="none" stroke="#e41e26"/></svg>info@tidy4all.com</div>
  </div>
  <div class="abs fcol" style="left:330px;width:160px">
    <h4>FAQ's</h4>
    <ul><li>What kinds of dumpsters do we offer?</li><li>How much does a dumpster cost?</li><li>How much debris fits inside?</li><li>How long can we keep the dumpster?</li><li style="color:#fff">View FAQs</li></ul>
  </div>
  <div class="abs footer-brand">Tidy4All</div>
  <div class="abs copy">© 2015 Tidy4All &nbsp;|&nbsp; All rights reserved</div>
</footer>

</body>
</html>
```